Web Design for a Biotech Consulting Firm

We need a web site design for a new business based in Philadelphia called Verantel Dx. This is a consulting firm that will serve medical diagnostics industry, which is part of the life science/healthcare industry focusing on developing and marketing products that help in early detection, monitoring or management of diseases. Our consulting firm will help medical diagnostic companies to overcome key challenges in designing, evaluating and marketing new products.Our company name is Verantel Dx. Verantel is Latin word for "something" Dx represents diagnostics. The idea behind the name is that we help companies to transform the original, early product ideas ("nothing") into "something"; which is a product with full clinical utility that will help to improve health and well-being.The web site should use the visual feel of the logo (attached), be modern, simple and clean looking and represent creativity, innovation, scientific thinking and progress.
Updates

Wix Design is acceptable

Industry/Entity Type

Biotechnology

Coding

Coded - Design and coding required

Number of Pages Required

1 page

Font styles to use
Sans Serif

Requirements
Must have
• simple, clean look couple of pages
Should not have
• a lot of pages

```html
<!DOCTYPE html>
<html lang="en">
<head>
<meta charset="utf-8">
<title>Verantel Dx – Biotech Consulting Firm</title>
<link href="https://fonts.googleapis.com/css2?family=Quicksand:wght@400;500;600;700&display=swap" rel="stylesheet">
<style>
:root{
  --blue:#1e74d9;
  --blue-soft:#e8f1fb;
  --ink:#1d1f24;
  --body:#3a3d44;
  --muted:#6d7078;
  --line:#e3e6ea;
  --footer:#1b4760;
  --white:#ffffff;
}
*{margin:0;padding:0;box-sizing:border-box}
html,body{width:1200px;height:2989px;overflow:hidden}
body{font-family:"Quicksand",sans-serif;color:var(--ink);background:var(--white);position:relative}
.abs{position:absolute}
.hero-bg{position:absolute;left:0;top:0;width:1200px;height:706px;
  background:linear-gradient(135deg,#2b3d55 0%,#3d5d82 35%,#27476e 60%,#476a8f 100%);
  clip-path:polygon(0 0,1200px 0,1200px 607px,0 706px)}
.about-band{position:absolute;left:0;top:600px;width:1200px;height:672px;background:var(--blue-soft);z-index:-1}
.brand{position:absolute;display:flex;align-items:center;gap:10px;font-weight:600;white-space:nowrap;color:var(--white)}
.brand i{display:block;width:12px;height:12px;background:var(--blue)}
.nav{position:absolute;top:52px;left:505px;display:flex;font-size:16px;color:var(--white);font-weight:500}
.nav a{color:var(--white);text-decoration:none;padding:0 23px;height:35px;line-height:35px}
.nav a.active{background:var(--blue)}
.hero-title{position:absolute;top:240px;left:0;width:1200px;text-align:center;color:var(--white);font-size:57px;font-weight:700}
.hero-sub{position:absolute;top:318px;left:0;width:1200px;text-align:center;color:var(--white);font-size:18px;line-height:26px;font-weight:500}
.btn{position:absolute;background:var(--blue);color:var(--white);font-size:14px;font-weight:500;text-align:center;text-decoration:none}
.frame{position:absolute;border:2px solid var(--blue)}
.photo{position:absolute}
.sec-box{position:absolute;border:2px solid var(--blue);border-right:none}
.sec-box::before,.sec-box::after{content:"";position:absolute;right:0;width:2px;height:10px;background:var(--blue)}
.sec-box::before{top:-2px}.sec-box::after{bottom:-2px}
.sec-title{position:absolute;font-size:28px;font-weight:500;white-space:nowrap;color:var(--ink)}
.sec-title span{color:var(--blue)}
.about-text{position:absolute;left:643px;top:906px;width:420px;font-size:14.5px;line-height:25.5px;color:var(--body);font-weight:500}
.card{position:absolute;border:2px solid #eef0f2;background:var(--white);text-align:center}
.card .icon{width:70px;height:70px;border:1.5px solid var(--blue);margin:44px auto 0;display:flex;align-items:center;justify-content:center}
.card h3{font-size:17px;font-weight:600;margin-top:24px;color:var(--ink)}
.card p{font-size:11px;line-height:18px;color:var(--muted);margin:10px 6px 0;letter-spacing:-0.1px}
.reviews-bg{position:absolute;left:0;top:1781px;width:1200px;height:480px;
  background:radial-gradient(circle at 70% 45%,#d9e6f3 0%,#bcd1e7 45%,#a9c3e0 100%)}
.review{position:absolute;top:2005px;width:293px;height:185px;background:rgba(255,255,255,.94);text-align:center}
.review p{margin:55px 16px 0;font-size:12.5px;line-height:19px;color:var(--muted);font-weight:500}
.review b{display:block;margin-top:9px;color:var(--blue);font-size:15px;font-weight:600}
.avatar{position:absolute;top:1968px;width:81px;height:81px;border:2px solid var(--blue);background:linear-gradient(180deg,#c7d3e0,#5b6d84)}
.arrow{position:absolute;width:25px;height:24px;border:1.5px solid #8aa0b6}
.arrow.right{border-color:var(--blue)}
.partner{position:absolute;top:2449px;width:210px;height:119px;background:var(--white);box-shadow:0 3px 12px rgba(30,50,80,.1);display:flex;align-items:center;justify-content:center;gap:10px;font-size:22px;font-weight:700}
.partner i{display:block;width:30px;height:30px;border-radius:50%}
.footer{position:absolute;left:0;top:2651px;width:1200px;height:338px;background:radial-gradient(circle at 50% 30%,#24597a 0%,var(--footer) 60%,#173d53 100%);color:var(--white)}
.f-head{position:absolute;top:60px;font-size:16px;font-weight:700;color:var(--blue)}
.f-list{position:absolute;font-size:13px;font-weight:500;line-height:25.8px;list-style:none}
.f-item{position:absolute;font-size:13px;font-weight:500;line-height:19px}
.f-divider{position:absolute;left:142px;top:243px;width:916px;height:1px;background:rgba(255,255,255,.18)}
.copyright{position:absolute;top:271px;left:0;width:1200px;text-align:center;font-size:11.5px;color:rgba(255,255,255,.8)}
.copyright b{color:var(--white);font-weight:600}
</style>
</head>
<body>

<div class="hero-bg" role="img" aria-label="Blue-toned laboratory photo of glass flasks and test tubes"></div>
<div class="about-band"></div>

<div class="brand" style="left:142px;top:55px;font-size:22px"><i></i>Verantel Dx</div>

<nav class="nav">
  <a class="active">Home</a><a>About Us</a><a>Services</a><a>Innovations</a><a>Contact Us</a>
</nav>

<h1 class="hero-title">Biotech Consulting Firm</h1>
<p class="hero-sub">We Will Serve Medical Diagnostics Industry, Which Is Part Of The<br>Life Science/healthcare Industry.</p>
<a class="btn" style="left:550px;top:407px;width:128px;height:36px;line-height:36px">Read More</a>

<div class="frame" style="left:142px;top:790px;width:417px;height:408px"></div>
<div class="photo" style="left:190px;top:755px;width:409px;height:402px;background:linear-gradient(135deg,#d8e6f1 0%,#8fb4d3 45%,#2d7fc4 75%,#1d4f7e 100%)" role="img" aria-label="Gloved hand holding an Erlenmeyer flask with blue liquid beside a pipette"></div>

<div class="sec-box" style="left:643px;top:812px;width:60px;height:64px"></div>
<div class="sec-title" style="left:669px;top:826px">About <span>Verantel Dx</span></div>
<p class="about-text">We are a Biotech consulting firm and &nbsp;we will serve medical diagnostics industry, which is part of the life science/healthcare industry focusing on developing and marketing products that help in early detection, monitoring or management of diseases.</p>
<a class="btn" style="left:643px;top:1071px;width:129px;height:37px;line-height:37px">Read More</a>

<div class="sec-box" style="left:506px;top:1343px;width:60px;height:64px"></div>
<div class="sec-title" style="left:530px;top:1355px">Our <span>Services</span></div>

<div class="card" style="left:142px;top:1451px;width:217px;height:260px">
  <div class="icon"><svg width="38" height="38" viewBox="0 0 38 38" fill="none" stroke="#333" stroke-width="1.6"><rect x="6" y="4" width="26" height="20" rx="3"/><circle cx="14" cy="12" r="3"/><path d="M20 10h8M20 15h6M10 24v10M16 24v10M22 24v6"/></svg></div>
  <h3>Corporate Strategy</h3>
  <p>Lorem Ipsum is simply dummy text<br>of the printing and typesetting<br>industry.</p>
</div>
<div class="card" style="left:374px;top:1451px;width:217px;height:260px">
  <div class="icon"><svg width="38" height="38" viewBox="0 0 38 38" fill="none" stroke="#333" stroke-width="1.6"><path d="M6 8h10l3 3h13v20H6z"/><path d="M10 17h10M10 22h8M10 27h6"/><circle cx="27" cy="26" r="4"/></svg></div>
  <h3>Product Development</h3>
  <p>Lorem Ipsum is simply dummy text<br>of the printing and typesetting<br>industry.</p>
</div>
<div class="card" style="left:606px;top:1451px;width:217px;height:260px">
  <div class="icon"><svg width="40" height="38" viewBox="0 0 40 38" fill="none" stroke="#333" stroke-width="1.6"><circle cx="20" cy="9" r="6"/><path d="M20 6v6M3 22l7-5 6 3 4-2 4 2 6-3 7 5M10 25l6 6 4-2 4 2 6-6"/></svg></div>
  <h3>Business Development</h3>
  <p>Lorem Ipsum is simply dummy text<br>of the printing and typesetting<br>industry.</p>
</div>
<div class="card" style="left:840px;top:1451px;width:218px;height:260px">
  <div class="icon"><svg width="38" height="38" viewBox="0 0 38 38" fill="none" stroke="#333" stroke-width="1.6"><rect x="16" y="5" width="16" height="14"/><path d="M22 5v14M27 5v14M16 12h16"/><circle cx="13" cy="18" r="6"/><path d="M9 26v8h8"/></svg></div>
  <h3>Commercialization</h3>
  <p>Lorem Ipsum is simply dummy text<br>of the printing and typesetting<br>industry.</p>
</div>

<div class="reviews-bg" role="img" aria-label="Soft blue medical background with faint lab and healthcare icons"></div>
<div class="sec-box" style="left:469px;top:1853px;width:60px;height:64px"></div>
<div class="sec-title" style="left:492px;top:1866px">Customer <span>Reviews</span></div>

<div class="review" style="left:142px"><p>Lorem ipsum dolor sit amet, consectetuer adipiscing elit, sed diam nonummy nibh euismod tincidunt ut laoreet dolore magna aliquam erat volutpat.</p><b>Emma</b></div>
<div class="review" style="left:454px"><p>Lorem ipsum dolor sit amet, consectetuer adipiscing elit, sed diam nonummy nibh euismod tincidunt ut laoreet dolore magna aliquam erat volutpat.</p><b>Emma</b></div>
<div class="review" style="left:765px"><p>Lorem ipsum dolor sit amet, consectetuer adipiscing elit, sed diam nonummy nibh euismod tincidunt ut laoreet dolore magna aliquam erat volutpat.</p><b>Emma</b></div>
<div class="avatar" style="left:248px" role="img" aria-label="Customer portrait photo"></div>
<div class="avatar" style="left:559px" role="img" aria-label="Customer portrait photo"></div>
<div class="avatar" style="left:871px" role="img" aria-label="Customer portrait photo"></div>

<div class="arrow" style="left:81px;top:2084px"><svg width="22" height="21" viewBox="0 0 22 21"><path d="M13 5l-5 5.5 5 5.5" fill="none" stroke="#8aa0b6" stroke-width="1.4"/></svg></div>
<div class="arrow right" style="left:1094px;top:2084px"><svg width="22" height="21" viewBox="0 0 22 21"><path d="M9 5l5 5.5-5 5.5" fill="none" stroke="#1e74d9" stroke-width="1.4"/></svg></div>

<div class="sec-box" style="left:502px;top:2333px;width:61px;height:64px"></div>
<div class="sec-title" style="left:527px;top:2345px">Our <span>Partners</span></div>

<div class="partner" style="left:142px;color:#e06a1b">Emberfield <i style="background:#f08a2c"></i></div>
<div class="partner" style="left:377px;color:#1e74d9"><i style="background:#1e74d9"></i>Apexora</div>
<div class="partner" style="left:612px;color:#1a9a6a">Greenwing <i style="background:#1a9a6a"></i></div>
<div class="partner" style="left:847px;color:#2b2b2b"><i style="background:#f29a1f"></i>Hexavale</div>

<div class="arrow" style="left:81px;top:2511px"><svg width="22" height="21" viewBox="0 0 22 21"><path d="M13 5l-5 5.5 5 5.5" fill="none" stroke="#8aa0b6" stroke-width="1.4"/></svg></div>
<div class="arrow right" style="left:1094px;top:2511px"><svg width="22" height="21" viewBox="0 0 22 21"><path d="M9 5l5 5.5-5 5.5" fill="none" stroke="#1e74d9" stroke-width="1.4"/></svg></div>

<footer class="footer">
  <div class="brand" style="left:143px;top:93px;font-size:18px"><i style="width:10px;height:10px"></i>Verantel Dx</div>
  <p class="f-item" style="left:142px;top:148px;width:200px">Lorem ipsum dolor sit amet, consectetuer adipiscing elit, sed diam.</p>

  <div class="f-head" style="left:453px">Quick Links</div>
  <ul class="f-list" style="left:453px;top:95px"><li>Home</li><li>About Us</li><li>Services</li><li>Innovations</li><li>Contact Us</li></ul>

  <div class="f-head" style="left:670px">Our Information</div>
  <svg class="abs" style="left:670px;top:101px" width="12" height="16" viewBox="0 0 12 16"><path d="M6 0a6 6 0 0 0-6 6c0 4.5 6 10 6 10s6-5.5 6-10a6 6 0 0 0-6-6zm0 8.5a2.5 2.5 0 1 1 0-5 2.5 2.5 0 0 1 0 5z" fill="#fff"/></svg>
  <p class="f-item" style="left:692px;top:98px;width:180px">11223 Lorem ipsum dolar met ulorem, 3344</p>
  <svg class="abs" style="left:670px;top:158px" width="14" height="14" viewBox="0 0 14 14"><path d="M3 0l3 3.5-1.6 1.8a9 9 0 0 0 4.3 4.3L10.5 8 14 11l-2 2.7C6 13.5.5 8 .3 2z" fill="#fff"/></svg>
  <p class="f-item" style="left:692px;top:155px">+11 123 456 789</p>
  <svg class="abs" style="left:670px;top:198px" width="15" height="11" viewBox="0 0 15 11"><rect width="15" height="11" rx="1" fill="#fff"/><path d="M0 1l7.5 5L15 1" fill="none" stroke="#1b4760" stroke-width="1.2"/></svg>
  <p class="f-item" style="left:696px;top:192px">info@veranteldx.com</p>

  <div class="f-head" style="left:966px">Follow Us</div>
  <p class="f-item" style="left:994px;top:100px">Linkfeed</p>
  <p class="f-item" style="left:994px;top:131px">Chirpline</p>

  <div class="f-divider"></div>
  <p class="copyright">© 2019 <b>Verantel Dx.</b> All rights reserved.</p>
</footer>

</body>
</html>
```